Veranix - Solution provider in business consulting

Veranix is a swiss based company providing solutions for developing markets. The business covers various fields of business consulting, such as supply chain, product costs, quality management and manufacturing management. The Business operates in a efficient, straight and solution oriented manner.
The final design should communicate these characteristics. Asian people as well as as western people shall identify the qualities of the company at first sight.
The customer needs business cards with a simple view but an recognizable design, printed in high quality. Engraved elements such as the globe or simple words are possible.
Available colors are: (RAL)
102/102/102
51/102/102
153/204/153
255/102/51
Font: Calibri

```html
<!DOCTYPE html>
<html lang="en">
<head>
<meta charset="utf-8">
<title>Veranix – Business Cards</title>
<link href="https://fonts.googleapis.com/css2?family=Carlito:wght@400;700&display=swap" rel="stylesheet">
<style>
  :root {
    --stage-top: #2a2a2a;
    --stage-bottom: #050505;
    --card-light: #f3f3f3;
    --card-dark: #6b6b6b;
    --globe-tone: #737373;
    --ink-logo: #666666;
    --ink-name: #555555;
    --ink-text: #222222;
    --icon: #555555;
    --white: #ffffff;
  }
  * { margin: 0; padding: 0; box-sizing: border-box; }
  html, body { width: 1200px; height: 900px; overflow: hidden; }
  body {
    background: linear-gradient(180deg, var(--stage-top) 0%, #151515 55%, var(--stage-bottom) 100%);
    font-family: "Carlito", "Calibri", sans-serif;
    position: relative;
  }
  .card {
    position: absolute;
    top: 184px;
    width: 303px;
    height: 490px;
    border-radius: 11px;
    overflow: hidden;
  }
  .card-front { left: 298px; background: var(--card-light); text-align: center; }
  .card-back { left: 645px; width: 305px; background: var(--card-dark); }

  .brand-word {
    position: absolute;
    left: 0; right: 0;
    top: 62px;
    font-size: 48px;
    font-weight: 400;
    color: var(--ink-logo);
    letter-spacing: 1px;
  }
  .person { position: absolute; left: 0; right: 0; top: 250px; }
  .person-name {
    font-size: 19px;
    font-weight: 700;
    color: var(--ink-name);
    letter-spacing: 0.5px;
  }
  .person-role { font-size: 14px; color: var(--ink-text); margin-top: 1px; }

  .contacts { position: absolute; left: 0; right: 0; top: 320px; list-style: none; }
  .contacts li {
    font-size: 14px;
    color: var(--ink-text);
    height: 20.5px;
    line-height: 20.5px;
    display: flex;
    justify-content: center;
    align-items: center;
    gap: 5px;
  }
  .contacts svg { width: 10px; height: 10px; fill: var(--icon); flex: none; }

  .address {
    position: absolute; left: 0; right: 0; top: 423px;
    font-size: 14px; line-height: 19px; color: var(--ink-text); font-style: normal;
  }

  .back-mark {
    position: absolute;
    left: 0; top: 0;
    width: 305px; height: 490px;
  }
  .back-word {
    position: absolute;
    left: 22px;
    top: 370px;
    font-size: 72px;
    font-weight: 400;
    color: var(--white);
    letter-spacing: 1.5px;
  }
</style>
</head>
<body>
  <section class="card card-front" aria-label="Business card front">
    <div class="brand-word">Veranix</div>

    <div class="person">
      <div class="person-name">MARCO FELDT</div>
      <div class="person-role">CEO</div>
    </div>

    <ul class="contacts">
      <li>
        <svg viewBox="0 0 10 10" aria-hidden="true"><path d="M2.5 0h5a1 1 0 0 1 1 1v8a1 1 0 0 1-1 1h-5a1 1 0 0 1-1-1V1a1 1 0 0 1 1-1zm0.6 1.2v6.6h3.8V1.2z"/></svg>
        +41 79 000 1234
      </li>
      <li>
        <svg viewBox="0 0 10 10" aria-hidden="true"><path d="M2 0.5l1.8 2-1 1.2c0.6 1.3 1.6 2.3 2.9 2.9l1.2-1 2 1.8-1.2 1.7C4.5 9 1 5.5 0.6 2z"/></svg>
        +41 71 000 5678
      </li>
      <li>
        <svg viewBox="0 0 10 10" aria-hidden="true"><path d="M0.5 2h9v6h-9z M1 2.4l4 3 4-3" /></svg>
        marco.feldt@veranix.ch
      </li>
      <li>
        <svg viewBox="0 0 10 10" aria-hidden="true"><circle cx="5" cy="5" r="4.6"/><path d="M5 0.6v8.8M0.6 5h8.8" stroke="#f3f3f3" stroke-width="0.7" fill="none"/></svg>
        www.veranix.ch
      </li>
    </ul>

    <address class="address">
      Veranix GmbH Lindenweg 14<br>
      8570 Talbach Switzerland
    </address>
  </section>

  <section class="card card-back" aria-label="Business card back">
    <svg class="back-mark" viewBox="0 0 305 490" role="img" aria-label="Faint engraved globe decoration">
      <circle cx="80" cy="180" r="176" fill="var(--globe-tone)"/>
    </svg>
    <div class="back-word">Veranix</div>
  </section>
</body>
</html>
```